KORV PTY LTD - Business Cards

Design a modern business card - using the attached Designs.
Same design as on the front, apart from the names/numbers/emails to be different.
We want the cards to be very glossy to stand out, do I think the simple black/white/metallic will be effective.
Both lots of details below:

Tom Wrenshaw
Director
tom_korv@nulvane.com
0438 274 093

Lewis Corbyn
Director
lewis_korv@nulvane.com
0419 385 642

Industry/Entity Type

Business

```html
<!DOCTYPE html>
<html lang="en">
<head>
<meta charset="utf-8">
<title>KORV PTY LTD – Business Cards</title>
<link rel="stylesheet" href="https://fonts.googleapis.com/css2?family=Noto+Serif&family=Open+Sans&display=swap">
<style>
  :root {
    --stage: #e6e4e1;
    --card-dark-1: #7b7f82;
    --card-dark-2: #3c3f42;
    --card-dark-3: #0d0e0f;
    --silver-1: #c9c9cc;
    --silver-2: #f4f4f6;
    --silver-3: #a9a8ad;
    --ink-light: #ffffff;
    --ink-soft: #e4e6e8;
    --band-grey: #9a9c9e;
    --band-black: #080808;
    --divider: rgba(255,255,255,0.25);
    --badge: #3a3c3f;
    --badge-ring: #b9bbbe;
    --mark-ghost: rgba(255,255,255,0.08);
  }
  * { box-sizing: border-box; margin: 0; padding: 0; }
  html, body { width: 1200px; height: 467px; overflow: hidden; }
  body {
    background: var(--stage);
    display: flex;
    align-items: center;
    justify-content: center;
    gap: 60px;
  }
  .card {
    position: relative;
    width: 520px;
    height: 300px;
    overflow: hidden;
    box-shadow: 0 6px 18px rgba(0,0,0,0.25);
  }
  .card--front {
    background: radial-gradient(ellipse at 25% 35%, var(--card-dark-1) 0%, var(--card-dark-2) 45%, var(--card-dark-3) 100%);
  }
  .card--back {
    background: linear-gradient(100deg, var(--silver-1) 0%, var(--silver-2) 30%, var(--silver-3) 55%, var(--silver-2) 78%, var(--silver-1) 100%);
    display: flex;
    align-items: center;
    justify-content: center;
  }
  .brand-mark {
    display: flex;
    align-items: center;
    gap: 12px;
    font-family: "Noto Serif", serif;
    font-weight: 400;
    letter-spacing: 3px;
  }
  .brand-mark__dot {
    border-radius: 50%;
    background: var(--badge);
    border: 3px solid var(--badge-ring);
  }
  .card--front .brand-mark {
    position: absolute;
    left: 48px;
    top: 112px;
    font-size: 40px;
    color: var(--ink-soft);
  }
  .card--front .brand-mark__dot { width: 34px; height: 34px; }
  .card--back .brand-mark { font-size: 64px; color: var(--badge); }
  .card--back .brand-mark__dot { width: 50px; height: 50px; }
  .divider {
    position: absolute;
    left: 258px;
    top: 40px;
    width: 1px;
    height: 150px;
    background: var(--divider);
  }
  .contact {
    position: absolute;
    left: 282px;
    top: 50px;
    color: var(--ink-light);
  }
  .contact__name {
    font-family: "Noto Serif", serif;
    font-size: 21px;
    font-weight: 400;
  }
  .contact__role {
    font-family: "Noto Serif", serif;
    font-size: 13px;
    margin-top: 6px;
  }
  .contact__list {
    list-style: none;
    margin-top: 30px;
    font-family: "Open Sans", sans-serif;
    font-size: 14px;
  }
  .contact__item { display: flex; align-items: center; gap: 8px; margin-bottom: 4px; }
  .contact__icon { width: 12px; height: 12px; fill: var(--ink-light); }
  .footer-bands { position: absolute; left: 0; bottom: 0; width: 520px; height: 100px; }
  .ghost-mark {
    position: absolute;
    right: 40px;
    bottom: 72px;
    font-family: "Noto Serif", serif;
    font-size: 30px;
    letter-spacing: 3px;
    color: var(--mark-ghost);
  }
</style>
</head>
<body>
  <section class="card card--front" aria-label="Business card front">
    <div class="brand-mark"><span class="brand-mark__dot"></span><span>KORV</span></div>
    <div class="divider"></div>
    <div class="contact">
      <h1 class="contact__name">Lewis Corbyn</h1>
      <p class="contact__role">Director</p>
      <ul class="contact__list">
        <li class="contact__item">
          <svg class="contact__icon" viewBox="0 0 24 24"><path d="M6.6 10.8a15 15 0 0 0 6.6 6.6l2.2-2.2a1 1 0 0 1 1-.25 11.4 11.4 0 0 0 3.6.57 1 1 0 0 1 1 1V20a1 1 0 0 1-1 1A17 17 0 0 1 3 4a1 1 0 0 1 1-1h3.5a1 1 0 0 1 1 1c0 1.25.2 2.45.57 3.6a1 1 0 0 1-.25 1z"/></svg>
          <span>0419 385 642</span>
        </li>
        <li class="contact__item">
          <svg class="contact__icon" viewBox="0 0 24 24"><path d="M2 5h20v14H2z M2 5l10 8 10-8" fill="none" stroke="#fff" stroke-width="2"/></svg>
          <span>lewis_korv@nulvane.com</span>
        </li>
      </ul>
    </div>
    <span class="ghost-mark">KORV</span>
    <svg class="footer-bands" viewBox="0 0 520 100" aria-hidden="true">
      <polygon points="290,28 520,28 520,100 0,100 0,62 258,62" fill="var(--band-black)"/>
      <polygon points="0,66 254,66 238,80 0,80" fill="var(--band-grey)"/>
    </svg>
  </section>

  <section class="card card--back" aria-label="Business card back">
    <div class="brand-mark"><span class="brand-mark__dot"></span><span>KORV</span></div>
  </section>
</body>
</html>
```